Business Card Design

I already have a company logo for my company. I have a logo for the manufacturer we represent. I want a professional business card design.

```html
<!DOCTYPE html>
<html lang="en">
<head>
<meta charset="utf-8">
<title>Business Card – Beacon Alert Systems</title>
<link rel="stylesheet" href="https://fonts.googleapis.com/css2?family=Montserrat:wght@700;800&family=Open+Sans:wght@400;600&display=swap">
<style>
  :root {
    --stage: #1b1b1d;
    --card-dark: #222125;
    --brand-red: #e31e2a;
    --brand-red-deep: #c9141f;
    --brand-orange: #f05a2a;
    --brand-gold: #c9962a;
    --text-light: #f4f4f4;
  }
  * { box-sizing: border-box; margin: 0; padding: 0; }
  html, body {
    width: 1200px; height: 780px; overflow: hidden;
    background: var(--stage);
  }
  .sheet {
    width: 1200px; height: 780px;
    display: flex; align-items: center; justify-content: center; gap: 40px;
  }
  .card {
    position: relative;
    width: 560px; height: 320px;
    border-radius: 20px;
    overflow: hidden;
  }

  /* back side */
  .card-back {
    background: var(--brand-red);
    border: 2px solid var(--brand-red-deep);
  }
  .card-back .pattern-fill {
    position: absolute; inset: 0;
    background: linear-gradient(160deg, var(--brand-orange) 0%, var(--brand-red) 45%, var(--brand-red-deep) 100%);
  }
  .card-back .corner-name {
    position: absolute; right: 34px; top: 70px;
    display: flex; align-items: center; gap: 5px;
    font-family: "Montserrat", sans-serif; font-weight: 800;
    font-size: 9px; letter-spacing: 0.5px;
    color: var(--text-light); text-transform: uppercase;
  }
  .corner-name .dot {
    width: 10px; height: 10px; border-radius: 50%; background: var(--text-light);
  }

  /* front side */
  .card-front {
    background: var(--card-dark);
    border: 2px solid var(--brand-red);
  }
  .company-mark {
    position: absolute; left: 40px; top: 110px; width: 220px;
    display: flex; align-items: center; gap: 10px;
  }
  .company-mark .dot {
    flex: none; width: 30px; height: 30px; border-radius: 50%; background: var(--brand-red);
  }
  .company-mark .company-name {
    font-family: "Montserrat", sans-serif; font-weight: 800;
    font-size: 22px; line-height: 1.1; text-transform: uppercase;
    color: var(--text-light);
  }
  .divider {
    position: absolute; left: 282px; top: 62px;
    width: 2px; height: 180px; background: var(--brand-gold);
  }
  .contact {
    position: absolute; left: 306px; top: 52px; right: 20px;
    font-family: "Open Sans", sans-serif; color: var(--text-light);
  }
  .person-name {
    font-family: "Montserrat", sans-serif; font-weight: 800;
    font-size: 25px; line-height: 1.1; letter-spacing: 0.3px;
  }
  .person-name .first { color: var(--brand-red); }
  .person-name .last { color: var(--brand-gold); }
  .job-title { font-size: 14px; margin-top: 3px; }
  .address { font-size: 13px; line-height: 1.35; margin-top: 14px; }
  .channels { list-style: none; margin-top: 14px; font-size: 13px; line-height: 1.6; }
  .channels li { display: flex; align-items: center; gap: 8px; }
  .channels svg { width: 12px; height: 12px; flex: none; }
  .edge-bands { position: absolute; left: 0; bottom: 0; width: 560px; height: 60px; }
</style>
</head>
<body>
<main class="sheet">

  <section class="card card-back" aria-label="Card back">
    <div class="pattern-fill" role="img" aria-label="Repeating pattern of brand marks in red and orange"></div>
    <div class="corner-name"><span class="dot"></span>Beacon Alert Systems</div>
  </section>

  <section class="card card-front" aria-label="Card front">
    <div class="company-mark">
      <span class="dot"></span>
      <span class="company-name">Beacon Alert Systems</span>
    </div>

    <div class="divider"></div>

    <div class="contact">
      <h1 class="person-name"><span class="first">Marta</span> <span class="last">Kovalenko</span></h1>
      <p class="job-title">Managing Director</p>
      <p class="address">1480 Maple Ridge Ave. Suite<br>310 Dallas, TX 75201</p>
      <ul class="channels">
        <li>
          <svg viewBox="0 0 24 24" aria-hidden="true"><path fill="#e31e2a" d="M6.6 10.8a15.1 15.1 0 0 0 6.6 6.6l2.2-2.2a1 1 0 0 1 1-.25 11.4 11.4 0 0 0 3.6.57 1 1 0 0 1 1 1V20a1 1 0 0 1-1 1A17 17 0 0 1 3 4a1 1 0 0 1 1-1h3.5a1 1 0 0 1 1 1c0 1.25.2 2.45.57 3.57a1 1 0 0 1-.25 1z"/></svg>
          (555) 204-1187
        </li>
        <li>
          <svg viewBox="0 0 24 24" aria-hidden="true"><path fill="#e31e2a" d="M3 5h18a1 1 0 0 1 1 1v12a1 1 0 0 1-1 1H3a1 1 0 0 1-1-1V6a1 1 0 0 1 1-1zm1 2v.5l8 5 8-5V7l-8 5z"/></svg>
          info@beaconalert.example
        </li>
        <li>
          <svg viewBox="0 0 24 24" aria-hidden="true"><circle cx="12" cy="12" r="10" fill="#e31e2a"/><path d="M2 12h20M12 2c3 3 3 17 0 20M12 2c-3 3-3 17 0 20" stroke="#222125" stroke-width="1.5" fill="none"/></svg>
          www.beaconalert.example
        </li>
      </ul>
    </div>

    <svg class="edge-bands" viewBox="0 0 560 60" aria-hidden="true">
      <polygon points="330,12 560,12 560,24 318,24" fill="#c9962a"/>
      <polygon points="0,36 300,36 282,52 0,52" fill="#e31e2a"/>
    </svg>
  </section>

</main>
</body>
</html>
```